Roofing Contractor business card redesign

I want to redesign my business card with a fresh, eye catching concept

Target Market(s)

Residential Roofing Clients, potential employees, and subcontractors.

Industry/Entity Type

Business

Colors

Designer to choose colors to be used in the design.

Requirements
Nice to have
• I just want something that's more pleasing to the eye. You can use a combination of either / or of my logos.

```html
<!DOCTYPE html>
<html lang="en">
<head>
<meta charset="utf-8">
<title>Solid Ridge General Contractors – Business Card</title>
<link rel="stylesheet" href="https://fonts.googleapis.com/css2?family=Fira+Sans+Condensed:wght@500&family=Open+Sans:wght@400;700&display=swap">
<style>
  :root {
    --page-bg: #e9e6e3;
    --card-bg: #f6f4f2;
    --brown: #3a2220;
    --orange: #e8731c;
    --white: #ffffff;
  }
  * { box-sizing: border-box; margin: 0; padding: 0; }
  html, body {
    width: 1200px; height: 900px; overflow: hidden;
    background: var(--page-bg);
    font-family: "Open Sans", Arial, sans-serif;
  }
  .card {
    position: absolute; left: 100px; top: 140px;
    width: 1000px; height: 620px;
    background: var(--card-bg);
    overflow: hidden;
    box-shadow: 0 8px 28px rgba(0,0,0,0.18);
  }
  .figure-area { position: absolute; inset: 0; width: 1000px; height: 620px; }
  .identity {
    position: absolute; right: 52px; top: 38px; text-align: right;
  }
  .identity__name {
    font-family: "Fira Sans Condensed", "Arial Narrow", sans-serif;
    font-weight: 500; font-size: 46px; color: var(--brown); line-height: 1.1;
  }
  .identity__title {
    font-size: 25px; color: var(--orange); line-height: 1.5;
  }
  .brand {
    position: absolute; left: 350px; top: 262px; width: 340px;
    text-align: center; color: var(--brown); font-weight: 700;
  }
  .brand__row { display: flex; align-items: center; justify-content: center; gap: 12px; }
  .brand__dot { width: 36px; height: 36px; border-radius: 50%; background: var(--orange); }
  .brand__name { font-size: 48px; line-height: 1.1; }
  .brand__sub { font-size: 24px; line-height: 1.4; }
  .address {
    position: absolute; left: 57px; top: 306px;
    color: var(--white); font-size: 26px; line-height: 1.38;
  }
  .contacts {
    position: absolute; left: 57px; top: 444px; list-style: none;
    color: var(--white); font-size: 26px; line-height: 1.4;
  }
  .contacts li { display: flex; align-items: center; gap: 12px; }
  .contacts svg { width: 20px; height: 20px; fill: var(--white); flex: none; }
</style>
</head>
<body>
  <div class="card">
    <svg class="figure-area" viewBox="0 0 1000 620" role="img" aria-label="Area for a roofer silhouette in a hard hat holding a hammer">
      <path d="M0,0 H318 V400 Q318,424 342,424 H420 Q440,424 440,444 V572 Q440,580 450,580 H1000 V620 H0 Z"
            fill="var(--brown)"/>
      <path d="M318,0 V400 Q318,424 342,424 H420 Q440,424 440,444 V572 Q440,580 450,580 H1000"
            fill="none" stroke="var(--orange)" stroke-width="5"/>
    </svg>

    <div class="identity">
      <p class="identity__name">Dan Mercer</p>
      <p class="identity__title">Keller certified Roof Inspector</p>
      <p class="identity__title">Licensed Property Adjuster</p>
    </div>

    <div class="brand">
      <div class="brand__row">
        <span class="brand__dot"></span>
        <span class="brand__name">Solid Ridge</span>
      </div>
      <p class="brand__sub">General Contractors, Inc.</p>
    </div>

    <p class="address">4410 Alder Creek<br>Road Suite 118<br>Dallas, TX 75230</p>

    <ul class="contacts">
      <li><svg viewBox="0 0 20 20"><path d="M2 7c0-3 3-4 8-4s8 1 8 4l-3 1-1-2H6L5 8zM5 9h10l2 8H3z"/></svg>(555) 210-4800</li>
      <li><svg viewBox="0 0 20 20"><path d="M6 1h8a1 1 0 0 1 1 1v16a1 1 0 0 1-1 1H6a1 1 0 0 1-1-1V2a1 1 0 0 1 1-1zm1 3v11h6V4z"/></svg>(555) 318-2741</li>
      <li><svg viewBox="0 0 20 20"><path d="M2 4h16v12H2zm1 1v1l7 5 7-5V5z"/></svg>dan@solidridgetx.com</li>
      <li><svg viewBox="0 0 20 20"><circle cx="10" cy="10" r="8"/><path d="M2 10h16M10 2c3 3 3 13 0 16M10 2c-3 3-3 13 0 16" stroke="var(--brown)" stroke-width="1.4" fill="none"/></svg>www.SolidRidgeGC.com</li>
    </ul>
  </div>
</body>
</html>
```